Home Staging Company needs business card design

We're a home staging company called Brightly Settled Home Staging. We would like a business card design that includes aqua and gray. Our current logo of house within chair is fine but I find we almost always use the logo in one color. I'll upload images of front and back of our current card and our logo. Note that we have dropped "Solutions" from our company name and don't want to include it on the card.

Target Market(s)

Realtors and homeowners - people interested in selling their homes

Contact Information for Business Card

Marisol Thistlewood
Brightly Settled Home Staging
757-555-0193
www.brightlysettled.com
marisol@brightlysettled.com

Font styles to use
Serif
Script

Requirements
Must have
• My logo and contact details
• UPDATE***
• I forgot to say that the company name should be included on the front of the card somehow.

```html
<!DOCTYPE html>
<html lang="en">
<head>
<meta charset="utf-8">
<title>Brightly Settled Home Staging – Business Card</title>
<link rel="stylesheet" href="https://fonts.googleapis.com/css2?family=Playfair+Display:wght@400&family=Roboto+Condensed:wght@400&family=Mulish:wght@400&display=swap">
<style>
  :root {
    --backdrop: #b9b9b9;
    --charcoal: #3a3d41;
    --charcoal-tint: #44474b;
    --paper: #f3f3f3;
    --paper-tint: #e6e6e6;
    --aqua: #4fb3bf;
    --ink: #3b3e42;
    --ink-soft: #55585c;
    --front-text: #eeeeee;
  }
  * { margin: 0; padding: 0; box-sizing: border-box; }
  html, body { width: 1200px; height: 576px; overflow: hidden; }
  body { background: var(--backdrop); position: relative; font-family: "Mulish", sans-serif; }

  .card {
    position: absolute;
    top: 138px;
    width: 484px;
    height: 294px;
    border-radius: 14px;
    overflow: hidden;
  }
  .card--front { left: 82px; background: var(--charcoal); }
  .card--back { left: 602px; background: var(--paper); }

  .faint-disc {
    position: absolute;
    border-radius: 50%;
  }
  .card--front .faint-disc { width: 330px; height: 330px; left: 62px; top: -10px; background: var(--charcoal-tint); }
  .card--back .faint-disc { width: 200px; height: 200px; left: 290px; top: 110px; background: var(--paper-tint); }

  .front-name {
    position: absolute;
    left: 0; right: 0; top: 112px;
    text-align: center;
    font-family: "Playfair Display", serif;
    font-weight: 400;
    color: var(--front-text);
  }
  .front-name__main { display: block; font-size: 42px; line-height: 1; letter-spacing: -0.5px; }
  .front-name__sub { display: block; font-size: 16px; letter-spacing: 7px; margin-top: 14px; padding-left: 7px; }

  .front-web {
    position: absolute;
    left: 0; right: 0; bottom: 14px;
    text-align: center;
    font-size: 13px;
    color: var(--aqua);
  }

  .edge-tab {
    position: absolute;
    left: -14px; top: 47px;
    width: 28px; height: 48px;
    border-radius: 50%;
    background: var(--aqua);
  }

  .person { position: absolute; left: 22px; top: 49px; }
  .person__name {
    font-family: "Roboto Condensed", sans-serif;
    font-size: 19px;
    color: var(--ink);
  }
  .person__surname { color: var(--aqua); }
  .person__title { font-size: 11px; color: var(--ink-soft); margin-top: 6px; }

  .brand {
    position: absolute;
    right: 22px; top: 52px;
    display: flex; align-items: center; gap: 8px;
  }
  .brand__mark { width: 14px; height: 14px; border-radius: 50%; background: var(--aqua); }
  .brand__name {
    font-family: "Playfair Display", serif;
    font-weight: 400;
    font-size: 19px;
    color: var(--ink);
  }

  .contacts { position: absolute; left: 28px; top: 206px; list-style: none; }
  .contacts li {
    display: flex; align-items: center; gap: 10px;
    font-size: 12px; color: var(--ink);
    height: 17.5px;
  }
  .contacts svg { width: 11px; height: 11px; fill: none; stroke: var(--ink-soft); stroke-width: 1.4; }
</style>
</head>
<body>

  <section class="card card--front">
    <div class="faint-disc"></div>
    <h1 class="front-name">
      <span class="front-name__main">Brightly Settled</span>
      <span class="front-name__sub">HOME STAGING</span>
    </h1>
    <p class="front-web">www.brightlysettled.com</p>
  </section>

  <section class="card card--back">
    <div class="faint-disc"></div>
    <div class="edge-tab"></div>

    <div class="person">
      <h2 class="person__name">Marisol <span class="person__surname">Thistlewood</span></h2>
      <p class="person__title">Managing Director</p>
    </div>

    <div class="brand">
      <span class="brand__mark"></span>
      <span class="brand__name">Brightly Settled</span>
    </div>

    <ul class="contacts">
      <li>
        <svg viewBox="0 0 12 12" aria-hidden="true"><path d="M2 3.5 C2 2 3 1.5 6 1.5 S10 2 10 3.5 L8.5 4.5 L7.5 3.5 H4.5 L3.5 4.5 Z M3 6 H9 L10 10.5 H2 Z"/></svg>
        757-555-0193
      </li>
      <li>
        <svg viewBox="0 0 12 12" aria-hidden="true"><circle cx="6" cy="6" r="4.6"/><path d="M1.4 6 H10.6 M6 1.4 C3.8 4 3.8 8 6 10.6 M6 1.4 C8.2 4 8.2 8 6 10.6"/></svg>
        www.brightlysettled.com
      </li>
      <li>
        <svg viewBox="0 0 12 12" aria-hidden="true"><rect x="1.2" y="2.6" width="9.6" height="6.8"/><path d="M1.2 2.6 L6 6.6 L10.8 2.6"/></svg>
        marisol@brightlysettled.com
      </li>
    </ul>
  </section>

</body>
</html>
```